Redesign of LumoWordfind.com in Bootstrap 4

Current design of LumoWordfind.com is not responsive. We need to change it to latest version of Bootstrap 4 keeping essential elements in place.

Apart from home page, we need designs for http://www.lumowordfind.com/meaning/cat also.

Coding

Number of Pages Required

2 page

Colors
34a7d8

Requirements
Must have
• Bootstrap 4

```html
<!DOCTYPE html>
<html lang="en">
<head>
<meta charset="utf-8">
<title>LumoWordfind – Search, Save and Master Words</title>
<link rel="stylesheet" href="https://fonts.googleapis.com/css2?family=Oswald:wght@300;400&family=Roboto:wght@400;500&display=swap">
<style>
  :root {
    --brand: #34a7d8;
    --hero-bg: #23252d;
    --hero-text: #f2f2f2;
    --hint: #8c8f98;
    --input-bg: #2a2d36;
    --input-border: #3a3d47;
    --body-text: #2a2a2a;
    --muted: #777;
    --white: #ffffff;
    --book-light: #e8892f;
    --book-dark: #c4531b;
  }
  * { box-sizing: border-box; margin: 0; padding: 0; }
  html, body { width: 1200px; height: 928px; overflow: hidden; background: var(--white); }
  body { font-family: "Roboto", Arial, sans-serif; position: relative; }

  .hero {
    position: absolute; left: 0; top: 0; width: 1200px; height: 528px;
    background-color: var(--hero-bg);
    background-image: radial-gradient(rgba(255,255,255,0.035) 1px, transparent 1px);
    background-size: 4px 4px;
  }
  .brand-box {
    position: absolute; left: 131px; top: 1px; width: 104px; height: 104px;
    background: var(--white);
    display: flex; align-items: center; justify-content: center;
  }
  .brand-name {
    font-family: "Roboto", Arial, sans-serif; font-weight: 500; font-size: 14px;
    color: var(--brand);
  }
  .search { position: absolute; left: 379px; top: 24px; }
  .search-field {
    width: 325px; height: 40px; background: var(--input-bg);
    border: 1px solid var(--input-border); color: var(--hint);
    font-size: 13px; padding: 0 11px; line-height: 38px;
  }
  .search-button {
    position: absolute; left: 325px; top: 0; width: 42px; height: 40px;
    background: var(--brand); display: flex; align-items: center; justify-content: center;
  }
  .search-hint { position: absolute; left: 11px; top: 47px; font-size: 9px; color: var(--hint); white-space: nowrap; }
  .account-links { position: absolute; left: 925px; top: 22px; font-size: 10.5px; font-weight: 500; color: var(--brand); }
  .menu-toggle { position: absolute; left: 1046px; top: 18px; width: 22px; height: 15px; }
  .menu-toggle span { display: block; height: 2px; background: #e6e6e6; margin-bottom: 4.5px; }

  .hero-title {
    position: absolute; left: 132px; top: 204px;
    font-family: "Oswald", sans-serif; font-weight: 300; font-size: 35px; color: var(--hero-text);
    letter-spacing: -0.3px;
  }
  .features { position: absolute; left: 132px; top: 270px; list-style: none; }
  .features li {
    position: relative; padding-left: 23px; height: 28.8px; line-height: 20px;
    font-size: 14.5px; color: var(--hero-text);
  }
  .features li::before {
    content: ""; position: absolute; left: 2px; top: 6px; width: 8px; height: 8px;
    background: var(--brand); transform: rotate(45deg);
  }
  .features .free { color: var(--brand); }

  .hero-art {
    position: absolute; left: 682px; top: 198px; width: 364px; height: 290px;
    background: linear-gradient(135deg, var(--book-dark), var(--book-light) 60%, #e9d3b0);
    border-radius: 14px;
  }

  .tidbit { position: absolute; left: 0; top: 528px; width: 1200px; text-align: center; }
  .tidbit-title {
    margin-top: 46px; font-family: "Oswald", sans-serif; font-weight: 400;
    font-size: 53px; line-height: 64px; color: var(--brand);
  }
  .tidbit-rule { width: 32px; height: 4px; background: var(--brand); margin: 10px auto 0; }
  .tidbit-word { margin-top: 44px; font-size: 19px; color: var(--muted); }
  .tidbit-text {
    width: 450px; margin: 12px auto 0; font-size: 17.6px; line-height: 27.2px; color: var(--body-text);
  }
</style>
</head>
<body>
  <header class="hero">
    <div class="brand-box"><span class="brand-name">LumoWordfind</span></div>

    <div class="search">
      <div class="search-field">Enter a word or phrase</div>
      <div class="search-button">
        <svg width="20" height="20" viewBox="0 0 20 20" aria-hidden="true">
          <circle cx="8" cy="8" r="6" fill="none" stroke="#fff" stroke-width="2.2"/>
          <line x1="12.5" y1="12.5" x2="18" y2="18" stroke="#fff" stroke-width="2.4" stroke-linecap="round"/>
        </svg>
      </div>
      <div class="search-hint">(eg. tone, summary, music)</div>
    </div>

    <div class="account-links">Login | Register</div>
    <div class="menu-toggle"><span></span><span></span><span></span></div>

    <h1 class="hero-title">Search, Save and Master Words</h1>
    <ul class="features">
      <li>Search from more than 300,000 words and phrases</li>
      <li>Multiple usages to clarify the context</li>
      <li>Audio, phonetics, meanings, synonyms and antonyms</li>
      <li>Save the words to your personal deck and access from anywhere</li>
      <li>It's <span class="free">FREE</span></li>
    </ul>

    <div class="hero-art" role="img" aria-label="Illustration of an orange English dictionary book"></div>
  </header>

  <section class="tidbit">
    <h2 class="tidbit-title">English Tidbit</h2>
    <div class="tidbit-rule"></div>
    <p class="tidbit-word">gibe/jibe</p>
    <p class="tidbit-text">To "gibe" is to taunt. Gibe is however slowly going out of use. Jibe means to agree but is often used in the negative sense. Although the versions of the tricksters jibed, the police officer suspected that there was something wrong.</p>
  </section>
</body>
</html>
```